New website for out outstanding veterinary training center

We already have a beautiful logo with nice colors and we are now looking for a breathtaking modern website to present our training center and future corses held there. A section to book open courses should also be available.

We are planing the realize the website with Wordpress.
The following pages should be available:
- Startpage / Overview
- Page to present the different rooms and seating option
- Page where the rooms can be booked
- Page where recommended accommodation are presented
- Page to present and book corses
- contact page
- Impressum

Target Market(s)

European Union

Industry/Entity Type

Education, Veterinary medicine

Number of Pages Required

5+ page

Font styles to use
Sans Serif

Colors
00AB8E
00BBA5
67D7C9
C6EFE9
E9F9F6

Requirements
Must have
• The website must be clear and easy to read. The colors form the logos should be used for the design.
Should not have
• To playful design. The page is not for a veterinary practice. we are a training center for veterinarians!

```html
<!DOCTYPE html>
<html lang="en">
<head>
<meta charset="utf-8">
<title>Vetora Training Center</title>
<link href="https://fonts.googleapis.com/css2?family=Lato:wght@400;700;900&family=Roboto:wght@400;500&display=swap" rel="stylesheet">
<style>
:root{
  --teal:#1a9488;
  --teal-dark:#137a70;
  --plum:#5a4957;
  --plum-dark:#4c3d4a;
  --ink:#222;
  --text:#555;
  --muted:#888;
  --line:#cfcfcf;
  --white:#fff;
}
*{box-sizing:border-box;margin:0;padding:0}
html,body{width:1200px;height:3459px;overflow:hidden}
body{font-family:Roboto,Arial,sans-serif;color:var(--text);background:var(--white);position:relative}
.wrap{position:absolute;left:111px;width:977px}
h1,h2,h3,h4,.nav a,.btn{font-family:Lato,Arial,sans-serif}

/* top bar */
.topbar{position:absolute;top:0;left:0;width:1200px;height:43px;background:var(--plum)}
.topbar .welcome{position:absolute;left:112px;top:13px;color:#fff;font:700 15px Lato,sans-serif}
.lang{position:absolute;left:918px;top:0;width:170px;height:43px;background:#fff;display:flex;align-items:center;justify-content:center;gap:8px;font-size:15px;color:#333}
.flag{width:22px;height:14px;background:repeating-linear-gradient(#c33 0 2px,#fff 2px 4px);position:relative}
.flag:before{content:"";position:absolute;left:0;top:0;width:10px;height:8px;background:#3b4a8a}

/* header */
.header{position:absolute;top:43px;left:0;width:1200px;height:127px;background:#fff}
.brand{position:absolute;left:140px;top:50px;display:flex;align-items:center;gap:8px;font:700 22px Lato,sans-serif;color:var(--teal)}
.brand i{width:28px;height:28px;border-radius:50%;background:var(--teal);display:block}
.contact-top{position:absolute;top:50px;right:113px;display:flex;gap:22px;font-size:15px;color:#444}
.contact-top span{display:flex;align-items:center;gap:5px}
.contact-top .sep{width:1px;height:16px;background:#ccc}

/* nav */
.nav{position:absolute;top:146px;left:111px;width:977px;height:51px;background:var(--teal);display:flex;align-items:center;z-index:3;clip-path:polygon(28px 0,100% 0,100% 100%,0 100%)}
.nav a{color:#fff;text-decoration:none;font-weight:700;font-size:16px;height:51px;line-height:51px;padding:0 15px}
.nav a.active{background:var(--plum);padding:0 14px 0 45px;margin-left:0;clip-path:polygon(28px 0,100% 0,100% 100%,0 100%)}
.nav .login{position:absolute;right:0;top:0;width:172px;background:var(--plum);text-align:center;clip-path:polygon(0 0,80% 0,100% 100%,0 100%);display:flex;align-items:center;justify-content:center;gap:5px}

/* hero */
.hero{position:absolute;top:170px;left:0;width:1200px;height:793px;background:linear-gradient(100deg,#eae7e1 0%,#dcd8d0 40%,#c7cfc6 70%,#e6e4de 100%)}
.hero-copy{position:absolute;left:111px;top:283px}
.hero h1{font-weight:900;font-size:64px;color:#111;letter-spacing:-1px}
.hero p{font-size:15px;line-height:31px;color:#222;margin-top:6px;width:540px}
.btn{display:inline-block;background:var(--teal);color:#fff;font-weight:700;font-size:16px;text-transform:uppercase}
.hero .btn{margin-top:26px;padding:0 27px;height:50px;line-height:50px}
.arrow{position:absolute;top:372px;width:50px;height:50px;border:1px solid #555;display:flex;align-items:center;justify-content:center}

/* sections */
.sec-title{text-align:center;font-weight:900;font-size:43px;color:#222}
.sec-title:after{content:"";display:block;width:84px;height:7px;border-radius:4px;background:var(--teal);margin:14px auto 0}
.who-title{position:absolute;top:1036px;left:0;width:1200px}
.who-lead{position:absolute;top:1125px;left:150px;width:900px;text-align:center;font-size:15px;line-height:31px;color:#444}
.who-img{position:absolute;top:1214px;left:111px;width:474px;height:397px;background:linear-gradient(135deg,#3f6fae 0%,#d9b88a 50%,#e9e9ee 100%);box-shadow:0 2px 6px rgba(0,0,0,.2)}
.who-text{position:absolute;top:1252px;left:617px;width:473px}
.who-text h3{font-weight:400;font-size:21px;color:#333}
.who-text p{font-size:13px;line-height:28px;color:#777;margin-top:16px}
.who-text p+p{margin-top:14px}
.ticks{list-style:none;margin-top:22px}
.ticks li{font-size:15px;line-height:30px;color:#666;display:flex;align-items:center;gap:6px}

.courses{position:absolute;top:1697px;left:0;width:1200px;height:698px;background:linear-gradient(180deg,#3a3a2e 0%,#2f3a22 50%,#22301a 100%)}
.courses .sec-title{color:#fff;margin-top:74px}
.card{position:absolute;top:183px;width:317px;height:427px;background:#fff;border-radius:4px;padding:6px}
.card .pic{height:193px;background:linear-gradient(120deg,#e8e6e2,#cdd8e2 60%,#b99875)}
.card h4{font-weight:700;font-size:16px;line-height:24px;color:#333;margin:22px 10px 0}
.card p{font-size:12.5px;line-height:24px;color:#888;margin:8px 10px 0}
.card .btn{margin:14px 10px 0;padding:0 26px;height:45px;line-height:45px}

.touch-title{position:absolute;top:2468px;left:0;width:1200px}
.form{position:absolute;top:2652px;left:111px;width:481px;display:grid;grid-template-columns:1fr 1fr;gap:13px 15px}
.field{height:55px;border:1px solid var(--line);border-radius:4px;padding:20px 13px;font-size:12.5px;color:#666}
.field.full{grid-column:1/3}
.field.msg{height:124px}
.submit{grid-column:1/3;height:55px;border-radius:4px;background:var(--teal);color:#fff;font:700 20px Lato,sans-serif;display:flex;align-items:center;justify-content:center}
.touch-img{position:absolute;top:2601px;left:638px;width:562px;height:498px;background:linear-gradient(160deg,#d8c9b6 0%,#2e6d9a 55%,#c9b08e 100%)}

.footer{position:absolute;top:3099px;left:0;width:1200px;height:360px;background:var(--plum);color:#fff}
.footer h3{font-weight:900;font-size:25px}
.footer h4{font-weight:700;font-size:16px}
.fcol{position:absolute;top:69px}
.fcol ul{list-style:none;margin-top:15px}
.fcol li{font-size:14px;line-height:32px;display:flex;align-items:center;gap:5px}
.about p{font-size:14px;line-height:26px;margin-top:14px;width:290px}
.footer .rule{position:absolute;left:111px;top:285px;width:977px;height:1px;background:#8c7c89}
.footer .copy{position:absolute;top:318px;width:1200px;text-align:center;font-size:13px}
</style>
</head>
<body>

<div class="topbar">
  <div class="welcome">WELCOME TO VETORA</div>
  <div class="lang"><span class="flag"></span>English</div>
</div>

<div class="header">
  <div class="brand"><i></i>Vetora</div>
  <div class="contact-top">
    <span><svg width="10" height="14" viewBox="0 0 10 14"><path d="M5 0a5 5 0 0 0-5 5c0 4 5 9 5 9s5-5 5-9a5 5 0 0 0-5-5zm0 7a2 2 0 1 1 0-4 2 2 0 0 1 0 4z" fill="#1a9488"/></svg>123, Lorem ipsum dolor sit amet, consectetur</span>
    <span class="sep"></span>
    <span><svg width="13" height="13" viewBox="0 0 24 24"><path d="M6.6 10.8a15 15 0 0 0 6.6 6.6l2.2-2.2c.3-.3.7-.4 1-.2 1.1.4 2.3.6 3.6.6.6 0 1 .4 1 1V20c0 .6-.4 1-1 1A17 17 0 0 1 3 4c0-.6.4-1 1-1h3.5c.6 0 1 .4 1 1 0 1.3.2 2.5.6 3.6.1.3 0 .7-.2 1z" fill="#1a9488"/></svg>123-456-7890</span>
  </div>
</div>

<nav class="nav">
  <a class="active">HOME</a>
  <a>WHO WE ARE</a>
  <a>OUR COURSES</a>
  <a>GET IN TOUCH</a>
  <a>CONTACT</a>
  <a class="login"><svg width="14" height="14" viewBox="0 0 16 16"><circle cx="8" cy="8" r="8" fill="#fff"/><circle cx="8" cy="6" r="2.6" fill="#5a4957"/><path d="M3.5 13a5 4 0 0 1 9 0" fill="#5a4957"/></svg>LOG IN</a>
</nav>

<section class="hero" role="img" aria-label="Veterinarian leaning over a desk with a laptop beside a dog skeleton model in a bright clinic room">
  <div class="hero-copy">
    <h1>VETORA</h1>
    <p>Sed ut perspiciatis unde omnis iste natus error sit accusantium doloremque laudantium, totam rem aperiam, eaque ipsa quae ab illo</p>
    <span class="btn">Get Started</span>
  </div>
  <div class="arrow" style="left:22px"><svg width="26" height="18" viewBox="0 0 26 18"><path d="M9 1 1 9l8 8M1 9h24M9 5v8" stroke="#444" stroke-width="2" fill="none"/></svg></div>
  <div class="arrow" style="right:26px"><svg width="26" height="18" viewBox="0 0 26 18"><path d="M17 1l8 8-8 8M25 9H1M17 5v8" stroke="#444" stroke-width="2" fill="none"/></svg></div>
</section>

<h2 class="sec-title who-title">WHO WE ARE</h2>
<p class="who-lead">Lorem ipsum dolor sit amet, consectetur adipiscing elit, sed do eiusmod tempor incididunt ut labore et dolore magna aliqua. Ut enim ad minim veniam, quis nostrud exercitation ullamco laboris nisi ut aliquip ex ea commodo consequat.</p>
<div class="who-img" role="img" aria-label="Puppy and kitten resting together on an examination table with a vet behind"></div>
<div class="who-text">
  <h3>Lorem ipsum dolor sit amet, consectetur</h3>
  <p>Sed ut perspiciatis unde omnis iste natus error sit voluptatem accusantium doloremque laudantium, totam rem aperiam, eaque ipsa quae ab illo inventore veritatis et quasi architecto beatae vitae dicta sunt explicabo.</p>
  <p>Sed ut perspiciatis unde omnis iste natus error sit voluptatem accusantium doloremque laudantium, totam rem aperiam,</p>
  <ul class="ticks">
    <li><svg width="14" height="14" viewBox="0 0 14 14"><circle cx="7" cy="7" r="7" fill="#1a9488"/><path d="M3.8 7.2 6 9.3l4.2-4.4" stroke="#fff" stroke-width="1.8" fill="none"/></svg>Lorem ipsum dolor sit amet, consectetur adipiscing</li>
    <li><svg width="14" height="14" viewBox="0 0 14 14"><circle cx="7" cy="7" r="7" fill="#1a9488"/><path d="M3.8 7.2 6 9.3l4.2-4.4" stroke="#fff" stroke-width="1.8" fill="none"/></svg>Lorem ipsum dolor sit amet, consectetur adipiscing</li>
    <li><svg width="14" height="14" viewBox="0 0 14 14"><circle cx="7" cy="7" r="7" fill="#1a9488"/><path d="M3.8 7.2 6 9.3l4.2-4.4" stroke="#fff" stroke-width="1.8" fill="none"/></svg>Lorem ipsum dolor sit amet, consectetur adipiscing</li>
  </ul>
</div>

<section class="courses" role="img" aria-label="Dark green background of a dog and cat in tall grass">
  <h2 class="sec-title">OUR COURSES</h2>
  <div class="card" style="left:113px">
    <div class="pic" role="img" aria-label="Vet teaching beside a dog skeleton model"></div>
    <h4>Lorem ipsum dolor sit amet, consectetur sit amet, consectetur</h4>
    <p>Lorem ipsum dolor sit amet, adipiscing elit, sed do eiusmod tempor incididunt ut labore et dolore magna aliqua.</p>
    <span class="btn">Buy Now</span>
  </div>
  <div class="card" style="left:443px">
    <div class="pic" role="img" aria-label="Vet examining a dog skeleton model"></div>
    <h4>Lorem ipsum dolor sit amet, consectetur sit amet, consectetur</h4>
    <p>Lorem ipsum dolor sit amet, adipiscing elit, sed do eiusmod tempor incididunt ut labore et dolore magna aliqua.</p>
    <span class="btn">Buy Now</span>
  </div>
  <div class="card" style="left:772px">
    <div class="pic" role="img" aria-label="Vet and pet owner with a dog on the floor"></div>
    <h4>Lorem ipsum dolor sit amet, consectetur sit amet, consectetur</h4>
    <p>Lorem ipsum dolor sit amet, adipiscing elit, sed do eiusmod tempor incididunt ut labore et dolore magna aliqua.</p>
    <span class="btn">Buy Now</span>
  </div>
</section>

<h2 class="sec-title touch-title">GET IN TOUCH</h2>
<div class="form">
  <div class="field">First Name</div>
  <div class="field">Last Name</div>
  <div class="field">Email Address</div>
  <div class="field">Phone Number</div>
  <div class="field full">Subject</div>
  <div class="field full msg">Message</div>
  <div class="submit">SUBMIT</div>
</div>
<div class="touch-img" role="img" aria-label="Smiling veterinarian in blue scrubs holding a pug on an examination table"></div>

<footer class="footer">
  <div class="fcol about" style="left:111px">
    <h3>ABOUT</h3>
    <p>Sed ut perspiciatis unde omnis iste natus error sit voluptatem accusantium doloremque laudantium, totam rem aperiam,</p>
  </div>
  <div class="fcol" style="left:530px;top:76px">
    <h4>QUICK LINKS</h4>
    <ul><li>Home</li><li>Who we are</li><li>Our Courses</li><li>Get in touch</li><li>Contact</li></ul>
  </div>
  <div class="fcol" style="left:710px;top:76px;width:230px">
    <h4>CONTACT</h4>
    <ul>
      <li style="align-items:flex-start">123, Lorem ipsum dolor sit amet, consectetur adipiscing</li>
      <li>123-456-7890</li>
      <li>info@vetora-training.com</li>
    </ul>
  </div>
  <div class="fcol" style="left:1002px;top:76px">
    <h4>HELP US</h4>
    <ul><li>Privacy Policy</li><li>FAQ</li><li>Information</li></ul>
  </div>
  <div class="rule"></div>
  <div class="copy">© 2021 All Rights Reserved</div>
</footer>

</body>
</html>
```